Tech business card design

We need an amazing business card design for our new business 'Pexla' a marketing tech startup based in Sydney, Australia. We provide an online marketplace for businesses to search and buy advertising media, connect with service providers and learn more about marketing. We wish to communicate 'cool tech', reliability and professionalism and design based around our logo.

Target Market(s)

Business Owners

Contact Information for Business Card

Name
Position
Email Address
Website
Phone Number

Font styles to use
Other font styles liked:
• Avenir & Avenir Next

Colors

Designer to choose colors to be used in the design.

```html
<!DOCTYPE html>
<html lang="en">
<head>
<meta charset="utf-8">
<title>Pexla Business Card</title>
<link href="https://fonts.googleapis.com/css2?family=Lato:wght@400&family=Montserrat:wght@700;800&display=swap" rel="stylesheet">
<style>
  :root {
    --navy: #0d0c3a;
    --navy-accent: #3d4180;
    --paper: #ffffff;
    --ink-soft: #55565c;
    --backdrop: #6b6b6b;
  }
  * { margin: 0; padding: 0; box-sizing: border-box; }
  html, body { width: 1200px; height: 802px; overflow: hidden; }
  body { background: var(--backdrop); position: relative; }

  .card {
    position: absolute;
    top: 274px;
    width: 443px;
    height: 265px;
  }
  .card--front { left: 136px; background: var(--paper); }
  .card--back { left: 624px; background: var(--navy); }

  .front-band {
    position: absolute; left: 0; top: 0;
    width: 45px; height: 100%;
    background: var(--navy);
  }
  .front-band-line {
    position: absolute; left: 45px; top: 0;
    width: 5px; height: 100%;
    background: var(--navy-accent);
  }

  .brand-name {
    position: absolute;
    font-family: "Montserrat", sans-serif;
    font-weight: 800;
    font-size: 58px;
    line-height: 1;
    letter-spacing: -1px;
    white-space: nowrap;
  }
  .card--front .brand-name { right: 47px; top: 44px; color: var(--navy); }
  .card--back .brand-name { left: 0; width: 100%; text-align: center; top: 104px; color: var(--paper); }

  .holder {
    position: absolute; left: 75px; top: 147px;
  }
  .holder-name {
    font-family: "Montserrat", sans-serif;
    font-weight: 700;
    font-size: 18px;
    line-height: 20px;
    color: var(--navy);
    letter-spacing: 0.2px;
    white-space: nowrap;
  }
  .holder-role {
    font-family: "Lato", sans-serif;
    font-size: 13px;
    line-height: 14px;
    color: var(--ink-soft);
  }

  .contact-list {
    position: absolute; left: 75px; top: 192px;
    list-style: none;
    font-family: "Lato", sans-serif;
    font-size: 12.5px;
    line-height: 16px;
    color: var(--ink-soft);
  }
  .contact-item { display: flex; align-items: center; gap: 5px; white-space: nowrap; }
  .contact-icon { width: 10px; height: 10px; fill: var(--navy); flex: none; }
</style>
</head>
<body>
  <section class="card card--front">
    <div class="front-band"></div>
    <div class="front-band-line"></div>
    <div class="brand-name">Pexla</div>

    <div class="holder">
      <div class="holder-name">DANIEL REEVE</div>
      <div class="holder-role">Managing Director</div>
    </div>

    <ul class="contact-list">
      <li class="contact-item">
        <svg class="contact-icon" viewBox="0 0 10 10" aria-hidden="true"><path d="M1 2.5C1 1.5 2.5 1 5 1s4 .5 4 1.5V4H7V3H3v1H1z"/><rect x="2" y="5" width="6" height="4" rx="0.5"/></svg>
        <span>044-987 654 321</span>
      </li>
      <li class="contact-item">
        <svg class="contact-icon" viewBox="0 0 10 10" aria-hidden="true"><path d="M0.5 2h9v6h-9z"/><path d="M0.5 2L5 5.5 9.5 2" fill="none" stroke="#fff" stroke-width="0.9"/></svg>
        <span>hello@pexla.net</span>
      </li>
      <li class="contact-item">
        <svg class="contact-icon" viewBox="0 0 10 10" aria-hidden="true"><circle cx="5" cy="5" r="4.5"/><path d="M3 3.2c1 .2 1.6 1 1.2 2-.4.8.4 1.6 1 2.4M6.5 2.2c-.3.8.3 1.4 1.2 1.4" fill="none" stroke="#fff" stroke-width="0.8"/></svg>
        <span>www.pexlamarket.com</span>
      </li>
    </ul>
  </section>

  <section class="card card--back">
    <div class="brand-name">Pexla</div>
  </section>
</body>
</html>
```